HOT TUB - SPAS service needs an business card

I need an business for my company who his specialise in a maintenance,water treatment and cleaning of Hot Tub - Spas for commercial and residential customers. The company operate mainly in the ski resort of Chamonix, Megève and St Gervais. The final product should communicate pure water, cleanest and professional for luxury property's.
I have upload a logo but any improvement on it is welcome.(color,size, details etc..) or any other idea. Thank you
Company Name: 58 BAINS
My name: Lucien Marchetti
Email: lucimarch@examplemail.net
Tel: +33 (0)6 71 58 29 64
Description to be on the card in french(first langage) and in English:
- Spas service
- Entretien, traitement eau, nettoyage.
- Maintenance, water treatment, cleaning.
Industry/Entity Type
Residential
Colors
Designer to choose colors to be used in the design.
Look and feel
Each slider illustrates characteristics of the customer's brand and the style your logo design should communicate.

```html
<!DOCTYPE html>
<html lang="fr">
<head>
<meta charset="utf-8">
<title>58 BAINS – Cartes de visite</title>
<link rel="stylesheet" href="https://fonts.googleapis.com/css2?family=Source+Sans+3:wght@400;600&display=swap">
<style>
  :root {
    --page: #eef1f4;
    --water-light: #4cb0f5;
    --water-mid: #2797ec;
    --water-deep: #1a7fdc;
    --navy: #1565c8;
    --white: #ffffff;
  }
  * { box-sizing: border-box; margin: 0; padding: 0; }
  html, body { width: 1200px; height: 1133px; overflow: hidden; }
  body {
    background: var(--page);
    font-family: "Source Sans 3", "Myriad Pro", Arial, sans-serif;
    color: var(--white);
    position: relative;
  }
  .card {
    position: absolute;
    width: 887px;
    height: 506px;
    overflow: hidden;
    box-shadow: 0 3px 10px rgba(0,0,0,.18);
  }
  .card--front { left: 38px; top: 38px; }
  .card--back { left: 270px; top: 583px; }
  .water-texture {
    position: absolute; inset: 0;
    background: radial-gradient(ellipse at 30% 20%, var(--water-light), var(--water-mid) 55%, var(--water-deep));
  }

  /* brand name on its ground line */
  .brand {
    position: absolute;
    border-bottom: 3px solid var(--white);
    display: flex; align-items: center; justify-content: center; gap: 18px;
    padding-bottom: 22px;
    font-size: 64px; font-weight: 600; letter-spacing: 2px; line-height: 1;
  }
  .brand__square { width: 24px; height: 24px; border: 3px solid var(--white); }
  .card--front .brand { left: 146px; width: 609px; top: 100px; }
  .card--back .brand { left: 109px; width: 684px; top: 174px; }

  .person-name {
    position: absolute; left: 497px; top: 352px;
    font-size: 32px; font-weight: 600;
  }
  .contact-band {
    position: absolute; left: 0; right: 0; top: 448px; height: 58px;
    background: var(--navy);
    display: flex; align-items: center;
    padding-left: 80px;
    font-size: 28px;
  }
  .contact-item { display: flex; align-items: center; gap: 10px; }
  .contact-item + .contact-item { margin-left: 18px; }
  .contact-item svg { width: 24px; height: 24px; }

  .services {
    position: absolute; left: 0; right: 0; top: 350px;
    text-align: center;
  }
  .services__title { font-size: 31px; font-weight: 600; margin-bottom: 8px; }
  .services__list { font-size: 31px; line-height: 43px; list-style: none; }
</style>
</head>
<body>
  <section class="card card--front">
    <div class="water-texture" role="img" aria-label="Photo de gouttes d'eau sur fond bleu"></div>
    <div class="brand"><span class="brand__square"></span>58 BAINS</div>
    <p class="person-name">Lucien Marchetti</p>
    <div class="contact-band">
      <span class="contact-item">
        <svg viewBox="0 0 24 24" aria-hidden="true"><path d="M6.6 2.5l3 3.2-1.8 2.6c1.2 2.8 3.3 4.9 6 6.1l2.6-1.8 3.2 3-1.6 3.2C11.4 18.6 5.4 12.6 3.2 4.1z" fill="none" stroke="#fff" stroke-width="1.8"/></svg>
        +33 (0)6 71 58 29 64
      </span>
      <span class="contact-item">
        <svg viewBox="0 0 24 24" aria-hidden="true"><rect x="2" y="6" width="20" height="13" fill="#fff"/><path d="M2 6l10 8 10-8" fill="none" stroke="#1565c8" stroke-width="1.6"/></svg>
        lucimarch@examplemail.net
      </span>
    </div>
  </section>

  <section class="card card--back">
    <div class="water-texture" role="img" aria-label="Photo de gouttes d'eau sur fond bleu"></div>
    <div class="brand"><span class="brand__square"></span>58 BAINS</div>
    <div class="services">
      <h2 class="services__title">SPAS SERVICES</h2>
      <ul class="services__list">
        <li>• Entretien &nbsp;• traitement eau &nbsp;• nettoyage</li>
        <li>• Maintenance &nbsp;• water treatment &nbsp;• cleaning.</li>
      </ul>
    </div>
  </section>
</body>
</html>
```